Exclusive beauty salon needs a price list or services booklet

I need a new very attractive flyer for my beauty salon, containing information on the different services and their prices.
In attachment you can find a pdf of the "old" one, but I'd love to have a beautifully designed new one!
I'd love to have a booklet in format 148 x 148 mm, or in US format, containing 12 or 16 pages, but if you can offer other nice looking designs they are welcome!
The services that need to come in the booklet with their prices can all be found on my website: www.atelierverano.be, starting with
Gelaatsverzorging
Wimperverlenging
Suikerontharing
Wimperlifting
Permanente Make Up
Airbrush Tanning

Target Market(s)

woman from 20 to 89 years old

Industry/Entity Type

Beauty Salon

Font styles to use
Sans Serif

Colors

Designer to choose colors to be used in the design.

Requirements
Must have
• a classy nice look, it must contain details about the services from my beauty salon and their prices, and nice pictures.
• The Names, prices and explanations of the services can easily be found on my website: www.atelierverano.be
Nice to have
• In attachment you can find the "old" price list in pdf, what I need now is a "new booklet" with the new logo and updated services price list.
• I need a very nice and attractive looking booklet, classy chique, Paris chique, looking very expensive.
Should not have
• Not too much colors, not too curly, but still feminine

```html
<!DOCTYPE html>
<html lang="nl">
<head>
<meta charset="utf-8">
<title>Wimperverlenging – brochure spread</title>
<link href="https://fonts.googleapis.com/css2?family=Didact+Gothic&family=Lustria&display=swap" rel="stylesheet">
<style>
  :root {
    --backdrop: #d9d9d9;
    --page: #f3f3f3;
    --page-edge: #e6e6e6;
    --ink: #2b2b2b;
    --teal: #4fb3ac;
    --teal-soft: #7cc7c1;
    --rule: #cfcfcf;
    --skin-light: #f2d9cb;
    --skin-mid: #e3b9a3;
    --skin-deep: #c98f78;
    --blush: #e9c9c9;
  }
  * { margin: 0; padding: 0; box-sizing: border-box; }
  html, body { width: 1200px; height: 900px; overflow: hidden; }
  body {
    background: var(--backdrop);
    font-family: "Didact Gothic", sans-serif;
    color: var(--ink);
    position: relative;
  }
  .spread {
    position: absolute;
    left: 80px;
    top: 188px;
    width: 1040px;
    height: 524px;
    display: flex;
  }
  .page { width: 520px; height: 524px; position: relative; overflow: hidden; }

  /* left page */
  .page--text {
    background: linear-gradient(90deg, var(--page) 0%, var(--page) 88%, var(--page-edge) 100%);
  }
  .page__photo-band {
    position: absolute; left: 0; top: 0; width: 100%; height: 110px;
    background: linear-gradient(180deg, var(--blush) 0%, #ead7d3 45%, rgba(243,243,243,0) 100%);
  }
  .page__title {
    position: absolute; top: 96px; width: 100%;
    text-align: center;
    font-family: "Lustria", serif;
    font-weight: 400; font-size: 29px; color: var(--ink);
  }
  .page__title-rule {
    position: absolute; top: 146px; left: 230px; width: 60px; height: 2px;
    background: var(--teal);
  }
  .page__subtitle {
    position: absolute; top: 162px; width: 100%; text-align: center;
    font-size: 15px; color: var(--ink);
  }
  .page__brand {
    position: absolute; top: 188px; width: 100%; text-align: center;
    font-size: 14px; color: var(--teal-soft);
  }
  .page__columns {
    position: absolute; top: 234px; left: 26px; width: 444px;
    display: flex; justify-content: space-between;
  }
  .page__column { width: 208px; }
  .page__column p {
    font-size: 11.5px; line-height: 26px;
    text-align: justify; hyphens: auto;
  }
  .page__footer {
    position: absolute; left: 26px; top: 470px; width: 444px;
    border-top: 1px solid var(--rule);
    display: flex; align-items: center; gap: 10px; padding-top: 6px;
  }
  .page__number {
    width: 24px; height: 22px; background: var(--teal); color: #fff;
    font-size: 12px; display: flex; align-items: center; justify-content: center;
  }
  .page__section { font-size: 12.5px; color: var(--teal-soft); }

  /* right page */
  .page--photo {
    background:
      radial-gradient(ellipse 40% 30% at 62% 50%, #fafafa 0%, #f3f0ef 60%, rgba(243,240,239,0) 100%),
      radial-gradient(ellipse 60% 70% at 65% 55%, var(--skin-light) 0%, var(--skin-mid) 60%, var(--skin-deep) 100%);
  }
</style>
</head>
<body>
  <main class="spread">
    <section class="page page--text">
      <div class="page__photo-band" role="img" aria-label="Close-up foto van gesloten ogen met lange, volle wimpers"></div>
      <h1 class="page__title">Wimperverlenging</h1>
      <div class="page__title-rule"></div>
      <p class="page__subtitle">individuele wimperverlenging</p>
      <p class="page__brand">Lumière Lashes</p>
      <div class="page__columns">
        <div class="page__column">
          <p>Lange, volle en gekrulde wimpers dankzij Lumière Lashes. Zijden wimpers worden één per één op uw eigen wimpers gekleefd. Mascara kan maar is overbodig. Lumière Lashes wimpers zijn ultralicht en zoveel natuurlijker dan kunststoffen wimperstrips, stukjes en plukjes. Door de exclusief ontwikkelde lijm blijven ze wekenlang in positie.</p>
        </div>
        <div class="page__column">
          <p>De sneldrogende lijm laat een plaatsing toe van ongeveer 60 wimpers per oog. Een vol effect, in een behandeling van slechts 1/2 uur. Na max. 4 weken laten bijwerken garandeert een optimaal en schitterend eindresultaat.</p>
          <p>De zijden wimpers zijn beschikbaar in verschillende lengtes, diktes en krulling of curves.</p>
        </div>
      </div>
      <footer class="page__footer">
        <span class="page__number">2</span>
        <span class="page__section">Wimperverlenging</span>
      </footer>
    </section>
    <section class="page page--photo" role="img" aria-label="Foto van een schoonheidsspecialiste die met pincetten wimperextensies plaatst bij een cliënte met een oogpad"></section>
  </main>
</body>
</html>
```